Business cards to launch an education platform

Hi,
I am looking at having new business cards designed.
I am a startup, developing a web platform for schools and university, the education world. It's an online assessment system.
I would like a card that looks classy, and that is using the colors and the font of my logo.

I have attached:
1) my logo
2) A business card that I have designed quickly so you can have all the information required in the card, but I really don't like it.
3) The font that I am using (Lato Regular) to design my web platform
4) Some screenshots of my web platform so you can have a look at the style that I have.

Target Market(s)

Major market: Education system: Schools and university
Minor markets: Business in general

Industry/Entity Type

Business

Contact Information for Business Card

Clara Fenwick
Director

M: 0437 518 902
E: clara.fenwick@amberLoomSystems.com.au

Requirements
Must have
• The colors of my logo

```html
<!DOCTYPE html>
<html lang="en">
<head>
<meta charset="utf-8">
<title>Amber Loom Systems — Business Cards</title>
<link rel="stylesheet" href="https://fonts.googleapis.com/css2?family=Lato:wght@400;700&display=swap">
<style>
  :root {
    --backdrop: #8d8e90;
    --card-paper: #e6e7e9;
    --navy: #0d3766;
    --brand-blue: #1c5291;
    --ink: #4a4b4e;
    --paper-text: #e9ebee;
    --back-muted: #cfd6e0;
  }
  * { margin: 0; padding: 0; box-sizing: border-box; }
  html, body {
    width: 1105px;
    height: 1200px;
    overflow: hidden;
    background: var(--backdrop);
    font-family: "Lato", sans-serif;
  }
  .sheet {
    position: relative;
    width: 1105px;
    height: 1200px;
  }
  .card {
    position: absolute;
    left: 182px;
    width: 747px;
    height: 427px;
    overflow: hidden;
  }
  .card--front { top: 119px; background: var(--card-paper); }
  .card--back { top: 637px; background: var(--navy); }

  .name-band {
    position: absolute;
    left: 0;
    top: 47px;
    width: 400px;
    height: 119px;
    background: var(--navy);
  }
  .holder-name {
    position: absolute;
    left: 42px;
    top: 31px;
    color: #ffffff;
    font-weight: 700;
    font-size: 26px;
    letter-spacing: 0.3px;
  }
  .holder-role {
    position: absolute;
    left: 42px;
    top: 68px;
    color: #dfe6ef;
    font-weight: 400;
    font-size: 19px;
    letter-spacing: 0.3px;
  }

  .brand {
    position: absolute;
    display: flex;
    align-items: center;
    gap: 14px;
  }
  .brand--front { left: 430px; top: 72px; }
  .brand__square {
    flex: none;
    width: 30px;
    height: 30px;
    background: var(--brand-blue);
  }
  .brand--front .brand__square { width: 56px; height: 56px; }
  .brand__name {
    font-weight: 400;
    font-size: 30px;
    letter-spacing: 1.5px;
    color: var(--brand-blue);
    white-space: nowrap;
  }
  .brand--front .brand__name {
    font-size: 29px;
    line-height: 32px;
    letter-spacing: 1.2px;
  }

  .contact {
    position: absolute;
    left: 0;
    right: 0;
    top: 334px;
    text-align: center;
    color: var(--ink);
  }
  .contact__mobile { font-weight: 700; font-size: 19px; line-height: 26px; }
  .contact__email { font-weight: 400; font-size: 19px; line-height: 26px; }

  .brand--back {
    left: 0;
    right: 0;
    top: 178px;
    justify-content: center;
  }
  .brand--back .brand__square { width: 40px; height: 40px; background: var(--paper-text); }
  .brand--back .brand__name { font-size: 40px; color: var(--paper-text); }

  .website {
    position: absolute;
    left: 0;
    right: 0;
    top: 357px;
    text-align: center;
    color: var(--back-muted);
    font-size: 20px;
    letter-spacing: 0.6px;
  }
</style>
</head>
<body>
<main class="sheet">
  <section class="card card--front" aria-label="Business card front">
    <div class="name-band">
      <p class="holder-name">CLARA FENWICK</p>
      <p class="holder-role">DIRECTOR</p>
    </div>
    <div class="brand brand--front">
      <span class="brand__square" aria-hidden="true"></span>
      <span class="brand__name">Amber Loom<br>Systems</span>
    </div>
    <div class="contact">
      <p class="contact__mobile">Mobile : 0437 518 902</p>
      <p class="contact__email">clara.fenwick@amberLoomSystems.com.au</p>
    </div>
  </section>

  <section class="card card--back" aria-label="Business card back">
    <div class="brand brand--back">
      <span class="brand__square" aria-hidden="true"></span>
      <span class="brand__name">Amber Loom Systems</span>
    </div>
    <p class="website">www.amberLoomSystems.com.au</p>
  </section>
</main>
</body>
</html>
```